Business cards for Harbourline Supply Pty Ltd that import building products into Australia from China
Target Market(s)
Business to Business
Industry/Entity Type
Business
Contact Information for Business Card
Front: Logo and Business Name
Rear:
Desmond Varrick
General Manager
Mobile: 0427 561 394
email: dessie@harbourlinesupply.com.au
alternative email: dessie@outbackworks.com.au
web: www.harbourlinesupply.com.au
Adelaide, Brisbane and Darwin
Colors
ec1f27
fbee3d

```html
<!DOCTYPE html>
<html lang="en">
<head>
<meta charset="utf-8">
<title>Harbourline Supply Pty Ltd — Business Cards</title>
<link rel="stylesheet" href="https://fonts.googleapis.com/css2?family=Montserrat:wght@500;600;700&display=swap">
<style>
  :root {
    --bg: #3a3a3a;
    --card: #050505;
    --red: #ec1f27;
    --yellow: #fbee3d;
    --white: #f4f4f4;
  }
  * { margin: 0; padding: 0; box-sizing: border-box; }
  html, body { width: 1200px; height: 864px; overflow: hidden; }
  body {
    background: var(--bg);
    font-family: "Montserrat", Arial, sans-serif;
    position: relative;
  }
  .card {
    position: absolute;
    left: 285px;
    width: 630px;
    height: 360px;
    background: var(--card);
    border-radius: 18px;
    box-shadow: 0 14px 30px rgba(0,0,0,0.45);
    color: var(--white);
  }
  .card--front { top: 52px; }
  .card--back { top: 452px; }

  .brand {
    position: absolute;
    display: flex;
    align-items: center;
    gap: 14px;
  }
  .brand__mark {
    width: 22px;
    height: 22px;
    background: var(--yellow);
  }
  .brand__name {
    font-weight: 700;
    color: var(--red);
    text-transform: uppercase;
    line-height: 1.05;
    letter-spacing: 1px;
  }
  .card--front .brand { left: 0; right: 0; top: 128px; justify-content: center; }
  .card--front .brand__name { font-size: 34px; }

  .cities {
    position: absolute;
    left: 0; right: 0; top: 262px;
    text-align: center;
    font-size: 15px;
    font-weight: 500;
    letter-spacing: 0.5px;
  }
  .cities .dot {
    display: inline-block;
    width: 5px; height: 5px;
    border-radius: 50%;
    background: var(--red);
    margin: 0 8px 3px;
  }

  .card--back .brand { left: 150px; top: 70px; }
  .card--back .brand__name { font-size: 28px; }

  .person {
    position: absolute;
    right: 330px;
    top: 222px;
    text-align: right;
  }
  .person__name {
    font-size: 29px;
    font-weight: 600;
    color: var(--red);
  }
  .person__role {
    font-size: 16px;
    font-weight: 500;
    margin-top: 4px;
  }
  .divider {
    position: absolute;
    left: 320px;
    top: 200px;
    width: 1.5px;
    height: 110px;
    background: var(--white);
  }
  .contacts {
    position: absolute;
    left: 340px;
    top: 206px;
    list-style: none;
    font-size: 14px;
    font-weight: 500;
  }
  .contacts li {
    display: flex;
    align-items: center;
    gap: 9px;
    height: 24px;
  }
  .contacts svg { width: 15px; height: 15px; flex: none; }
</style>
</head>
<body>

<section class="card card--front" aria-label="Card front">
  <div class="brand">
    <span class="brand__mark"></span>
    <span class="brand__name">Harbourline Supply<br>Pty Ltd</span>
  </div>
  <p class="cities">Adelaide<span class="dot"></span>Brisbane<span class="dot"></span>Darwin</p>
</section>

<section class="card card--back" aria-label="Card back">
  <div class="brand">
    <span class="brand__mark"></span>
    <span class="brand__name">Harbourline Supply<br>Pty Ltd</span>
  </div>

  <div class="person">
    <p class="person__name">Desmond Varrick</p>
    <p class="person__role">General Manager</p>
  </div>

  <span class="divider"></span>

  <ul class="contacts">
    <li>
      <svg viewBox="0 0 16 16" aria-hidden="true"><rect x="4" y="1" width="8" height="14" rx="1.5" fill="none" stroke="#fbee3d" stroke-width="1.6"/><circle cx="8" cy="12.5" r="0.9" fill="#fbee3d"/></svg>
      0427 561 394
    </li>
    <li>
      <svg viewBox="0 0 16 16" aria-hidden="true"><rect x="1" y="3.5" width="14" height="9" fill="#fbee3d"/><path d="M1 3.5 L8 9 L15 3.5" fill="none" stroke="#050505" stroke-width="1.3"/></svg>
      dessie@harbourlinesupply.com.au
    </li>
    <li>
      <svg viewBox="0 0 16 16" aria-hidden="true"><rect x="1" y="3.5" width="14" height="9" fill="#fbee3d"/><path d="M1 3.5 L8 9 L15 3.5" fill="none" stroke="#050505" stroke-width="1.3"/></svg>
      dessie@outbackworks.com.au
    </li>
    <li>
      <svg viewBox="0 0 16 16" aria-hidden="true"><g fill="none" stroke="#fbee3d" stroke-width="1.3"><circle cx="8" cy="8" r="6.5"/><ellipse cx="8" cy="8" rx="3" ry="6.5"/><path d="M1.5 8 H14.5 M2.5 4.8 H13.5 M2.5 11.2 H13.5"/></g></svg>
      www.harbourlinesupply.com.au
    </li>
  </ul>
</section>

</body>
</html>
```